Luxury Wine Label for New Startup Winery

We need a wine label for our new winery startup. We have worked with a local designer but do not feel the resulting label / logo have the elevation required to present our brand as a luxury wine. Our winery is called "Quailbrook Vineyards" and we are focused on extremely high quality hand crafted artisan and estate wines from the Pacific Northwest.
We would like to see designs that utilize a tree line, or other imagery that represents the "Quailbrook" part of our company name. Another interesting feature could be wood grain.
A logo will be required based on your design so please design with this in mind:
This logo should be consistent with the wine bottle label design, and should be representative of our high end exclusive wine while giving a sense of place (Oregon/ Pacific Northwest.)
I will supply an image of the design we received from our local designer, PLEASE NOTE: in general we do like wood grain and tree line concepts but feel the execution was poorly done.
ATTN: Logo design should be suitable for use on: Bottles (Red wine/rose/white wine), Bussiness cards, vehicle signage, business signage, etc
P.S.:
If you have a design that is not outside the box we are still interested in seeing it.
Label is for a burgundy style bottle with a label height of 3.5 - 4" and a width of 3.5-4"
any label <= 4"x4" and >=3.5"x3.5" will be acceptable:
HOWEVER Width should be greater than or equal to height due to the bottle format
Target Market(s)
Wine enthusiasts with adequate discretionary budgets to afford $100 bottles of wine.
Industry/Entity Type
Wine / Winery
Requirements
Must have
- A sense of luxury, a feel of exclusivity, and a theme consistent with our product and brand name
Nice to have
- Tree line, wood grain or other wood themes. Serif fonts
Should not have
- anything cheesy, off topic, hard to read script fonts or anything that makes the label hard to read from a few feet away or too busy

```html
<!DOCTYPE html>
<html lang="en">
<head>
<meta charset="utf-8">
<title>Quailbrook Vineyards – Syrah Label</title>
<link rel="stylesheet" href="https://fonts.googleapis.com/css2?family=Playfair+Display:wght@400;700&family=Josefin+Sans:wght@600&display=swap">
<style>
  :root {
    --paper: #ffffff;
    --label-black: #000000;
    --gold-light: #f4dc8a;
    --gold: #c9982f;
    --gold-deep: #7a4c14;
    --wood-dark: #3a1a10;
    --wood-mid: #6b3322;
    --wood-light: #8e4a31;
    --ink-white: #ffffff;
  }
  * { margin: 0; padding: 0; box-sizing: border-box; }
  html, body {
    width: 1111px;
    height: 1200px;
    overflow: hidden;
    background: var(--paper);
  }
  .canvas {
    position: relative;
    width: 1111px;
    height: 1200px;
    background: var(--paper);
  }
  .label-main {
    position: absolute;
    left: 134px;
    top: 152px;
    width: 842px;
    height: 683px;
    background: var(--label-black);
  }
  .label-main .frame {
    position: absolute;
    inset: 0;
    width: 842px;
    height: 683px;
  }
  .landscape-art {
    position: absolute;
    left: 214px;
    top: 104px;
    width: 368px;
    height: 235px;
    border-radius: 40% 50% 30% 30%;
    background: radial-gradient(ellipse at 45% 55%, var(--gold) 0%, var(--gold-deep) 45%, rgba(0,0,0,0) 75%);
    opacity: 0.85;
  }
  .brand-name {
    position: absolute;
    left: 0;
    right: 0;
    top: 389px;
    text-align: center;
    font-family: "Playfair Display", serif;
    font-weight: 700;
    font-size: 84px;
    line-height: 1;
    letter-spacing: 0.02em;
    color: var(--gold);
  }
  .brand-sub {
    position: absolute;
    left: 0;
    right: 0;
    top: 492px;
    text-align: center;
    font-family: "Playfair Display", serif;
    font-weight: 400;
    font-size: 39px;
    line-height: 1;
    letter-spacing: 0.46em;
    padding-left: 0.46em;
    color: var(--ink-white);
  }
  .label-varietal {
    position: absolute;
    left: 134px;
    top: 861px;
    width: 842px;
    height: 184px;
    background: var(--label-black);
  }
  .label-varietal .plate {
    position: absolute;
    inset: 0;
    width: 842px;
    height: 184px;
  }
  .varietal-name {
    position: absolute;
    left: 0;
    right: 0;
    top: 64px;
    text-align: center;
    font-family: "Josefin Sans", sans-serif;
    font-weight: 600;
    font-size: 74px;
    line-height: 1;
    letter-spacing: 0.2em;
    padding-left: 0.2em;
    color: var(--ink-white);
  }
</style>
</head>
<body>
<main class="canvas">
  <section class="label-main">
    <svg class="frame" viewBox="0 0 842 683" aria-hidden="true">
      <defs>
        <linearGradient id="goldLine" x1="0" y1="0" x2="1" y2="0">
          <stop offset="0" stop-color="#b8862b"/>
          <stop offset="0.5" stop-color="#f4dc8a"/>
          <stop offset="1" stop-color="#9a6a22"/>
        </linearGradient>
      </defs>
      <g fill="none" stroke="url(#goldLine)">
        <rect x="47" y="37" width="747" height="609" stroke-width="2"/>
        <rect x="56" y="46" width="729" height="591" stroke-width="1.5"/>
        <rect x="64" y="54" width="713" height="575" stroke-width="2"/>
      </g>
    </svg>
    <div class="landscape-art" role="img" aria-label="Gold engraved illustration of mountain peaks above a sloping line of evergreen trees"></div>
    <h1 class="brand-name">QUAILBROOK</h1>
    <p class="brand-sub">VINEYARDS</p>
  </section>

  <section class="label-varietal">
    <svg class="plate" viewBox="0 0 842 184" aria-hidden="true">
      <defs>
        <linearGradient id="woodTone" x1="0" y1="0" x2="1" y2="1">
          <stop offset="0" stop-color="#5a2a1b"/>
          <stop offset="0.35" stop-color="#8e4a31"/>
          <stop offset="0.65" stop-color="#6b3322"/>
          <stop offset="1" stop-color="#3a1a10"/>
        </linearGradient>
        <linearGradient id="goldEdge" x1="0" y1="0" x2="1" y2="0">
          <stop offset="0" stop-color="#b8862b"/>
          <stop offset="0.5" stop-color="#f4dc8a"/>
          <stop offset="1" stop-color="#a8741f"/>
        </linearGradient>
      </defs>
      <path role="img" aria-label="Polished walnut wood grain panel"
            d="M38,16 H804 A22,22 0 0 0 826,38 V147 A22,22 0 0 0 804,169 H38 A22,22 0 0 0 16,147 V38 A22,22 0 0 0 38,16 Z"
            fill="url(#woodTone)" stroke="url(#goldEdge)" stroke-width="6"/>
    </svg>
    <p class="varietal-name">SYRAH</p>
  </section>
</main>
</body>
</html>
```